Tellmora Corporate Stationery

Look for design of all new corporate stationery for an existing insurance broking business that is going through a redesign and move from older partners to younger family members. New Logo is attached. Company is Brisbane based.
Colours in the Logo is Hex #43bed8 and website features a lot of hex #17b8d8. Website front page "A plan to protect you" - headline. "Professional and Individual advice to protect your greatest assets" - tagline.

Stationery required: Business Cards, Letter head, Thank-you cards, Birthday cards, Presentation folders, With Compliment slips and a powerpoint template. We also would like to send a card to all customers with the something along of the lines of "something new".

Target Market(s)

Customers of Insurance business looking at superannuation, life and income protection insurance, investment advice and wills

Industry/Entity Type

Insurance Broker

Font styles to use
Other font styles liked:
• same as logo

Requirements
Must have
• The above designs for new stationery for the new business including:
• Business Cards, Letter head, Thank-you cards, Birthday cards, Presentation folders, With Compliment slips and a powerpoint template. We also would like to send a card to all customers with the something along of the lines of "something new".
Nice to have
• It is a new look - long time family business being passed to next generation - big focus on advice for YOU, individual advice etc..

```html
<!DOCTYPE html>
<html lang="en">
<head>
<meta charset="utf-8">
<title>Tellmora Business Card</title>
<link rel="stylesheet" href="https://fonts.googleapis.com/css2?family=Montserrat:wght@600;700&family=Open+Sans:wght@400;600&display=swap">
<style>
  :root {
    --teal: #43bed8;
    --teal-deep: #17b8d8;
    --teal-dark: #2a9fbc;
    --steel: #7d8084;
    --steel-light: #a3a5a8;
    --steel-dark: #5f6266;
    --paper: #ffffff;
    --paper-shade: #e9eaeb;
    --ink-grey: #4a4d51;
    --backdrop: #e4e2de;
  }
  * { margin: 0; padding: 0; box-sizing: border-box; }
  html, body {
    width: 1200px;
    height: 843px;
    overflow: hidden;
    background: var(--backdrop);
    font-family: "Open Sans", Arial, sans-serif;
  }
  .stage {
    position: relative;
    width: 1200px;
    height: 843px;
  }
  .card {
    position: absolute;
    left: 300px;
    width: 600px;
    height: 343px;
    border-radius: 3px;
    overflow: hidden;
    box-shadow: 0 8px 22px rgba(0,0,0,0.22);
  }
  .card-back {
    top: 55px;
    background: linear-gradient(135deg, var(--steel-dark) 0%, var(--steel) 45%, var(--steel-light) 100%);
  }
  .card-front {
    top: 445px;
    background: linear-gradient(120deg, var(--paper-shade) 0%, var(--paper) 55%, var(--paper-shade) 100%);
  }
  .card-shapes {
    position: absolute;
    inset: 0;
  }

  /* Back side */
  .back-name {
    position: absolute;
    top: 128px;
    left: 0;
    width: 100%;
    display: flex;
    justify-content: center;
    align-items: center;
    gap: 14px;
    font-family: "Montserrat", Arial, sans-serif;
    font-weight: 700;
    font-size: 38px;
    letter-spacing: 3px;
    color: var(--paper);
  }
  .back-dot {
    width: 22px;
    height: 22px;
    border-radius: 50%;
    background: var(--teal);
  }
  .back-web {
    position: absolute;
    top: 262px;
    width: 100%;
    text-align: center;
    font-size: 14px;
    letter-spacing: 5px;
    color: #f2f3f4;
  }

  /* Front side */
  .brand {
    position: absolute;
    top: 58px;
    right: 58px;
    display: flex;
    align-items: center;
    gap: 12px;
  }
  .brand-dot {
    width: 34px;
    height: 34px;
    border-radius: 50%;
    background: var(--teal);
  }
  .brand-name {
    font-family: "Montserrat", Arial, sans-serif;
    font-weight: 700;
    font-size: 34px;
    letter-spacing: 1px;
    color: var(--teal);
  }
  .holder {
    position: absolute;
    top: 152px;
    right: 70px;
    text-align: right;
  }
  .holder-name {
    font-family: "Montserrat", Arial, sans-serif;
    font-weight: 700;
    font-size: 19px;
    letter-spacing: 0.5px;
    color: var(--teal-deep);
  }
  .holder-role {
    margin-top: 3px;
    font-size: 14px;
    color: var(--ink-grey);
  }
  .contacts {
    position: absolute;
    top: 78px;
    left: 30px;
    list-style: none;
    color: var(--paper);
    font-size: 14px;
    line-height: 1;
  }
  .contacts li {
    display: flex;
    align-items: center;
    gap: 9px;
    height: 22px;
  }
  .contacts svg {
    width: 13px;
    height: 13px;
    flex: none;
    fill: var(--paper);
  }
  .contacts .address {
    margin-top: 2px;
    font-size: 13.5px;
  }
</style>
</head>
<body>
<main class="stage">

  <section class="card card-back" aria-label="Business card, back">
    <div class="back-name"><span class="back-dot"></span><span>TELLMORA</span></div>
    <p class="back-web">www.tellmora.com.au</p>
  </section>

  <section class="card card-front" aria-label="Business card, front">
    <svg class="card-shapes" viewBox="0 0 600 343" preserveAspectRatio="none" aria-hidden="true">
      <defs>
        <linearGradient id="tealPanel" x1="0" y1="0" x2="1" y2="1">
          <stop offset="0" stop-color="#2aaecb"/>
          <stop offset="0.55" stop-color="#43bed8"/>
          <stop offset="1" stop-color="#5cc9e0"/>
        </linearGradient>
        <linearGradient id="steelBand" x1="0" y1="0" x2="1" y2="1">
          <stop offset="0" stop-color="#6e7175"/>
          <stop offset="0.5" stop-color="#a6a8ab"/>
          <stop offset="1" stop-color="#76797d"/>
        </linearGradient>
      </defs>
      <polygon class="panel-teal" points="0,0 140,0 470,343 0,343" fill="url(#tealPanel)"/>
      <polygon class="band-steel" points="140,0 154,0 484,343 470,343" fill="url(#steelBand)"/>
    </svg>

    <ul class="contacts">
      <li>
        <svg viewBox="0 0 16 16" aria-hidden="true"><path d="M3.6 1.2l2.3 2.6-1.3 1.9c.9 2 2.5 3.6 4.5 4.5l1.9-1.3 2.6 2.3-1.4 2.6C6.3 14.5 1.5 9.7 1 3.7z"/></svg>
        <span>07 3184 2250</span>
      </li>
      <li>
        <svg viewBox="0 0 16 16" aria-hidden="true"><path d="M4.5 0h7a1 1 0 0 1 1 1v14a1 1 0 0 1-1 1h-7a1 1 0 0 1-1-1V1a1 1 0 0 1 1-1zm.7 2v10h5.6V2zM8 13a.9.9 0 1 0 0 1.8A.9.9 0 0 0 8 13z"/></svg>
        <span>0412 596 318</span>
      </li>
      <li>
        <svg viewBox="0 0 16 16" aria-hidden="true"><path d="M4 1h8v4H4zM1 6h14v6h-3v3H4v-3H1zm4 4v3.5h6V10z"/></svg>
        <span>07 3184 2251</span>
      </li>
      <li>
        <svg viewBox="0 0 16 16" aria-hidden="true"><path d="M0 3h16v10H0zm1.5 1.2L8 9l6.5-4.8V4.1H1.5z"/></svg>
        <span>daniel@tellmora.com.au</span>
      </li>
      <li>
        <svg viewBox="0 0 16 16" aria-hidden="true"><path d="M8 0a8 8 0 1 0 0 16A8 8 0 0 0 8 0zm0 1.5c.8 0 1.8 1.9 2.1 5.5H5.9C6.2 3.4 7.2 1.5 8 1.5zM1.6 9h2.8c.1 2 .5 3.8 1.1 4.9A6.5 6.5 0 0 1 1.6 9zm0-2a6.5 6.5 0 0 1 3.9-4.9C4.9 3.2 4.5 5 4.4 7zm6.4 7.5c-.8 0-1.8-1.9-2.1-5.5h4.2c-.3 3.6-1.3 5.5-2.1 5.5zm2.5-.6c.6-1.1 1-2.9 1.1-4.9h2.8a6.5 6.5 0 0 1-3.9 4.9zM11.6 7c-.1-2-.5-3.8-1.1-4.9A6.5 6.5 0 0 1 14.4 7z"/></svg>
        <span>www.tellmora.com.au</span>
      </li>
      <li class="address">
        <span>42 Wattle Street, Brisbane, QLD 4000</span>
      </li>
    </ul>

    <div class="brand">
      <span class="brand-dot"></span>
      <span class="brand-name">TELLMORA</span>
    </div>

    <div class="holder">
      <p class="holder-name">DANIEL REEVE</p>
      <p class="holder-role">CEO/Founder</p>
    </div>
  </section>

</main>
</body>
</html>
```